Varnex Consulting Business card design.

See our website www.varnexconsulting.example which will give you a good idea of what we are about. The font is called 'Play'.

I'd like a standout business card in keeping with the themes and branding on the website

Target Market(s)

professionals. HR directors

Industry/Entity Type

Business

Contact Information for Business Card

Varnex Consulting PO Box 3172 Merrowdale NSW 2291 1300 485 193 Gavin Threlkeld Principal email: career@varnexconsulting.example ABN: 71203948865

Font styles to use
Other font styles liked:
• Play

Requirements
Must have
• Must have same design colours and branding as website.
• On back I'd prefer a list of the things we do which appears below the name at the header on the website

```html
<!DOCTYPE html>
<html lang="en">
<head>
<meta charset="utf-8">
<title>Varnex Consulting – Business Card</title>
<link rel="stylesheet" href="https://fonts.googleapis.com/css2?family=Arimo:wght@400;700&display=swap">
<style>
  :root {
    --page-bg: #e9e7e3;
    --card-white: #ffffff;
    --card-grey: #d9dadc;
    --brand-blue: #1a98e0;
    --brand-navy: #1b2a38;
    --navy-light: #34495c;
    --ink: #1c2733;
    --muted: #5d6166;
  }
  * { box-sizing: border-box; margin: 0; padding: 0; }
  html, body {
    width: 1200px;
    height: 950px;
    overflow: hidden;
    background: var(--page-bg);
  }
  .stage {
    width: 1200px;
    height: 950px;
    display: flex;
    flex-direction: column;
    align-items: center;
    justify-content: center;
    gap: 30px;
  }
  .card {
    position: relative;
    width: 760px;
    height: 434px;
    background: linear-gradient(160deg, var(--card-white) 35%, var(--card-grey) 100%);
    box-shadow: 0 6px 18px rgba(0,0,0,0.18);
    overflow: hidden;
  }
  .company-name {
    font-family: "Arimo", sans-serif;
    font-weight: 700;
    color: var(--brand-navy);
    letter-spacing: 0;
    white-space: nowrap;
  }

  /* Front */
  .card-front .company-name {
    position: absolute;
    left: 56px;
    top: 56px;
    font-size: 52px;
    line-height: 1;
  }
  .person {
    position: absolute;
    left: 300px;
    top: 150px;
    font-family: "Arimo", sans-serif;
    text-align: center;
  }
  .person-name {
    font-size: 24px;
    font-weight: 700;
    color: var(--ink);
  }
  .person-role {
    font-size: 18px;
    color: var(--brand-blue);
    margin-top: 2px;
  }
  .contact-band {
    position: absolute;
    left: 0;
    right: 0;
    top: 218px;
    height: 104px;
    display: flex;
    gap: 4px;
    font-family: "Arimo", sans-serif;
    color: #ffffff;
  }
  .band-address {
    width: 380px;
    background: var(--brand-blue);
    padding: 20px 28px 0 0;
    text-align: right;
    font-size: 20px;
    line-height: 1.35;
  }
  .band-contact {
    flex: 1;
    background: linear-gradient(100deg, var(--brand-navy) 0%, var(--navy-light) 45%, var(--brand-navy) 100%);
    padding: 18px 0 0 28px;
    font-size: 19px;
  }
  .contact-line {
    display: flex;
    align-items: center;
    gap: 10px;
    height: 32px;
  }
  .contact-line svg { width: 20px; height: 20px; fill: #ffffff; flex: none; }
  .website {
    position: absolute;
    left: 70px;
    top: 350px;
    font-family: "Arimo", sans-serif;
    font-size: 20px;
    letter-spacing: 3px;
    color: var(--muted);
  }

  /* Back */
  .card-back .company-name {
    position: absolute;
    right: 70px;
    top: 158px;
    font-size: 46px;
    line-height: 1;
  }
  .services {
    position: absolute;
    right: 70px;
    top: 228px;
    font-family: "Arimo", sans-serif;
    font-size: 19px;
    letter-spacing: 1px;
    color: var(--muted);
  }
</style>
</head>
<body>
<main class="stage">
  <section class="card card-front" aria-label="Business card front">
    <div class="company-name">Varnex Consulting</div>
    <div class="person">
      <div class="person-name">Gavin Threlkeld</div>
      <div class="person-role">Principal</div>
    </div>
    <div class="contact-band">
      <div class="band-address">PO Box 3172 Merrowdale<br>NSW 2291</div>
      <div class="band-contact">
        <div class="contact-line">
          <svg viewBox="0 0 24 24" aria-hidden="true"><path d="M6.6 10.8a15.1 15.1 0 0 0 6.6 6.6l2.2-2.2a1 1 0 0 1 1-.25 11.4 11.4 0 0 0 3.6.57 1 1 0 0 1 1 1V20a1 1 0 0 1-1 1A17 17 0 0 1 3 4a1 1 0 0 1 1-1h3.5a1 1 0 0 1 1 1c0 1.25.2 2.45.57 3.6a1 1 0 0 1-.25 1z"/></svg>
          <span>1300 485 193</span>
        </div>
        <div class="contact-line">
          <svg viewBox="0 0 24 24" aria-hidden="true"><path d="M3 5h18a1 1 0 0 1 1 1v.4l-10 6.3L2 6.4V6a1 1 0 0 1 1-1zm-1 3.7 10 6.3 10-6.3V18a1 1 0 0 1-1 1H3a1 1 0 0 1-1-1z"/></svg>
          <span>career@varnexconsulting.example</span>
        </div>
      </div>
    </div>
    <div class="website">www.varnexconsulting.example</div>
  </section>

  <section class="card card-back" aria-label="Business card back">
    <div class="company-name">Varnex Consulting</div>
    <div class="services">Coaching | Leadership | Outplacement</div>
  </section>
</main>
</body>
</html>
```